physio rehab flyer for Vela Mend please

Specification:
Flyer is to be trifold from letter size (8.5 x 11)
-----------------------This may help you:--------------------------
I would like the look of :
clean, minimalistic look with mainly blue and green
san serif font
professional
The colors I like are blue (not the blue in the logo enclosed, I want a change, but more like the blue on my website logo) and light green.
This is my website: www.velamendgroup.ca just so you get an idea but it will be totally changed soon to a to be determined design.
I like the blue and green in file "sample 2" (enclosed)
I like the pictures in "sample 2" file enclosed
For inspiration, I like design of this brochure: http://www.brelford.ca/HarlowRehab/PatientsFamilies/Clinics_Tests/DKAP_Service/Documents/Brochure.pdf
Here's how I see the pages layout:
----[location: this should be the cover (outside, right panel of trifold)]-----
Vela Mend Logo
Integrated Injury Rehab
Evidence-based, one-on-one care to make your recovery fast and comfortable
www.velamendgroup.ca
---------------[location: inside, left panel]----------------------------------------
Our team leaders
[portrait here]
Harriet Olsavik, MD, FRCPC, MSC, CIME
Physiatrist
Dr. Olsavik specializes in injury rehab and sports medicine. She is highly trained having received her MD and Residency in Physiatry from Pellham Institute. Her passion is to help injured people get back to their life.
[portrait here]
Wendy Carstairs, PT
Physiotherapist
Wendy has over 10 years of experience as a Physiotherapist (5 in Canada). She has advanced training in orthopedics and manual therapy. She loves and relates well with people from the youngest to the most senior.
--------------------[location: inside, middle panel]-------------------------------
Our services
We provide integrated assessment and care from interprofessional team of regulated healthcare professionals with proven experience in injury rehabilitation:
physiatrists
sport medicine physicians
physiotherapists
chiropractors
massage therapists
acupuncturists
psychologists
We provide custom medical bracing, orthotics, orthopedic shoes, assistive devices, and medical stockings, all in one place.
----------------------[location: inside, right panel]-----------------------------------
Only registered physiotherapists
We strongly believe in consistency with your treatment plan. This means that you spend your time here one-on-one with your physiotherapist, not any students or assistants. You get consistent high quality care from a professional.
One-on-one attention
We book maximum 3 people per hour to ensure everyone gets adequate one-on-one time with their physiotherapist. This compares favorably with other clinics, who may book upwards of 5-6 per hour. The atmosphere is professional -balanced with friendly, caring and relaxed. Our highly qualified staff operate this way to help make your recovery faster and more enjoyable.
------------------------[location: outside, left panel]---------------------------------
The right rehab for your clients
Timely access to comprehensive assessment and treatment
Proven track record in injury rehabilitation
Convenient one-stop service
Customized treatment plans
Integrated, co-ordinated care
Evidence-based care applying leading best practices
Access to specialty clinics: Physiatry and Chronic Pain
-------------------------[location: outside, middle panel]--------------------------
Please call us 555-384-2096
for more information on injury rehabilitation
Vela Mend Group
1862 Wexmoor Rd., Unit 9
Scarborough, ON K4T 8B2
[Please include a line art map designed based on "map" file enclosed]
To make a referral for your clients, contact velamendgroup@corvamail.ca or fax: 555-384-2071. Thank you.
www.velamendgroup.ca
------------------------------------------------------------------------------------------------
Target Market(s)
family doctors, ER docs, lawyers, and general public age (20-50)
Industry/Entity Type
Health And Wellness
Requirements
Must have
- san serif font
- blue and green colors
- clean, sophisticated look
Nice to have
- consumer choice award badge either on front or back of trifold
- see above

```html
<!DOCTYPE html>
<html lang="en">
<head>
<meta charset="utf-8">
<title>Vela Mend – Integrated Injury Rehab Trifold</title>
<link rel="stylesheet" href="https://fonts.googleapis.com/css2?family=PT+Sans:ital,wght@0,400;0,700;1,400&family=PT+Sans+Narrow:wght@400;700&family=Crimson+Pro:wght@400;500&display=swap">
<style>
  :root {
    --blue: #2d6db3;
    --blue-mid: #4a86c5;
    --blue-light: #7fa8d6;
    --green: #9cc23c;
    --green-band: #c4dc7a;
    --panel-tint: #dfe7f1;
    --panel-tint-2: #e4ebf3;
    --rule-green: #b9d27a;
    --badge-red: #8c1c2c;
    --badge-gold: #d6a531;
    --page-bg: #ecebe8;
    --white: #ffffff;
    --ink-soft: #5c6f86;
  }
  * { margin: 0; padding: 0; box-sizing: border-box; }
  html, body { width: 1200px; height: 1000px; overflow: hidden; }
  body { background: var(--page-bg); font-family: "PT Sans", Arial, sans-serif; position: relative; }

  .sheet { position: absolute; width: 568px; height: 438px; background: var(--white);
    box-shadow: 0 6px 18px rgba(0,0,0,.18); overflow: hidden; }
  .sheet--outside { left: 12px; top: 211px; }
  .sheet--inside { left: 584px; top: 302px; width: 566px; }
  .panel { position: absolute; top: 0; height: 100%; overflow: hidden; }

  /* Outside left */
  .referral { left: 0; width: 190px; }
  .referral__band { position: absolute; inset: 0; }
  .referral__title { position: absolute; left: 26px; top: 50px; font-weight: 700; font-size: 14.5px; line-height: 18px; }
  .referral__title .t-light { color: var(--blue-light); }
  .referral__title .t-green { color: var(--green); }
  .referral__title .t-blue { color: var(--blue); }
  .benefits { position: absolute; left: 24px; top: 143px; width: 160px; list-style: none;
    font-family: "Crimson Pro", Georgia, serif; font-size: 10.5px; line-height: 15.6px; color: var(--blue); }
  .benefits li { position: relative; padding-left: 11px; }
  .benefits li::before { content: "»"; position: absolute; left: 0; }

  /* Outside middle */
  .contact { left: 190px; width: 188px; text-align: center; font-size: 8px; line-height: 10px; color: var(--blue); }
  .contact__call { position: absolute; top: 147px; width: 100%; }
  .contact__call strong { color: var(--green); font-weight: 700; }
  .contact__address { position: absolute; top: 187px; width: 100%; color: var(--ink-soft); }
  .contact__map { position: absolute; left: 36px; top: 238px; width: 116px; height: 92px;
    background: #eef3f9; border: 1px solid var(--blue-light); }
  .contact__referral { position: absolute; top: 339px; width: 100%; }
  .contact__referral strong { color: var(--green); font-weight: 700; display: block; }
  .contact__web { position: absolute; top: 391px; width: 100%; color: var(--ink-soft); }

  /* Front */
  .cover { left: 378px; width: 190px; }
  .cover__photo { position: absolute; inset: 0;
    background: linear-gradient(180deg, #b9c9dc 0%, #9fb1c4 40%, #7f8a86 70%, #c89a7c 100%); }
  .cover__swoosh { position: absolute; left: 0; bottom: 0; }
  .cover__title { position: absolute; left: 3px; top: 46px; font-weight: 700; font-size: 22px; line-height: 34px; }
  .cover__title .t-light { color: var(--blue-light); }
  .cover__title .t-green { color: var(--green); }
  .cover__title .t-blue { color: var(--blue); }
  .cover__tagline { position: absolute; left: 4px; top: 201px; width: 130px; font-size: 12.5px; line-height: 15.5px; color: var(--blue); }
  .cover__web { position: absolute; left: 7px; top: 399px; font-size: 9.5px; font-weight: 700; color: var(--green); white-space: nowrap; }

  .seal { position: absolute; width: 44px; height: 44px; border-radius: 50%;
    background: var(--badge-red); border: 5px solid var(--badge-gold); }
  .cover .seal { left: 10px; top: 340px; }

  .brand { position: absolute; display: flex; align-items: center; gap: 4px; white-space: nowrap;
    font-family: "PT Sans", Arial, sans-serif; font-weight: 700; font-style: normal; color: var(--blue); }
  .brand__dot { width: 9px; height: 9px; border-radius: 50%; background: var(--blue); }
  .cover .brand { right: 8px; top: 372px; font-size: 14px; }

  /* Inside left */
  .team { left: 0; width: 190px; background: var(--panel-tint); }
  .portrait { position: absolute; background: linear-gradient(160deg, #e8ecef, #c9d0d6); }
  .portrait--lead { left: 6px; top: 23px; width: 134px; height: 190px; }
  .portrait--second { left: 52px; top: 246px; width: 138px; height: 192px; }
  .member__name { position: absolute; font-weight: 700; font-size: 10.5px; color: #44576d; white-space: nowrap; }
  .member__cred { position: absolute; font-style: italic; font-size: 8px; line-height: 10px; color: var(--blue-mid); }
  .member__bio { position: absolute; font-weight: 700; font-size: 6.8px; line-height: 8.6px; color: var(--blue); }
  .m1 .member__name { left: 72px; top: 34px; }
  .m1 .member__cred { left: 72px; top: 47px; }
  .m1 .member__bio { left: 80px; top: 76px; width: 104px; text-align: right; }
  .team__rule { position: absolute; left: 0; top: 214px; width: 175px; height: 1px; background: var(--rule-green); }
  .m2 .member__name { left: 27px; top: 228px; }
  .m2 .member__cred { left: 27px; top: 242px; }
  .m2 .member__bio { left: 26px; top: 262px; width: 60px; }

  /* Inside middle */
  .services { left: 190px; width: 188px; }
  .services__photo { position: absolute; left: 0; top: 0; width: 188px; height: 145px;
    background: linear-gradient(135deg, #d8dde2 0%, #b6c8dc 45%, #2b2b2b 60%, #e2b9a2 80%); }
  .services__title { position: absolute; top: 164px; width: 100%; text-align: center;
    font-weight: 700; font-size: 12px; color: var(--green); font-variant: small-caps; letter-spacing: .3px; }
  .services__intro { position: absolute; left: 16px; top: 183px; width: 156px; font-size: 7.6px; line-height: 12px; color: var(--green); }
  .services__list { position: absolute; left: 34px; top: 236px; list-style: none; font-size: 7.6px; line-height: 11.5px; color: var(--green); }
  .services__list li::before { content: "»"; margin-right: 6px; font-size: 7px; }
  .services__rule { position: absolute; left: 12px; top: 333px; width: 164px; height: 1px; background: var(--rule-green); }
  .services__extras { position: absolute; left: 16px; top: 340px; width: 166px; font-family: "PT Sans Narrow", "PT Sans", sans-serif;
    font-style: italic; font-size: 12.5px; line-height: 18px; color: var(--blue); white-space: nowrap; }

  /* Inside right */
  .promise { left: 378px; width: 188px; background: var(--panel-tint-2); text-align: center;
    font-family: "PT Sans Narrow", "PT Sans", sans-serif; font-style: italic; font-size: 8.8px; line-height: 14px; color: var(--blue); }
  .promise__block { position: absolute; left: 17px; width: 154px; }
  .promise__block--first { top: 28px; }
  .promise__block--second { top: 172px; }
  .promise__rule { position: absolute; left: 0; width: 188px; height: 1px; background: var(--rule-green); }
  .promise .seal { left: 16px; top: 364px; }
  .promise .brand { left: 96px; top: 370px; font-size: 15px; }
</style>
</head>
<body>

<section class="sheet sheet--outside">
  <div class="panel referral">
    <svg class="referral__band" width="190" height="438" viewBox="0 0 190 438" aria-hidden="true">
      <path d="M0 138 C 60 100, 120 60, 190 52 L190 438 L0 438 Z" fill="var(--green-band)"/>
    </svg>
    <h2 class="referral__title">
      <span class="t-light">THE</span><br>
      <span class="t-green">RIGHT</span><br>
      <span class="t-light">REHAB FOR</span><br>
      <span class="t-blue">YOUR CLIENTS</span>
    </h2>
    <ul class="benefits">
      <li>Timely access to comprehensive assessment and treatment</li>
      <li>Proven track record in injury rehabilitation</li>
      <li>Convenient one-stop service</li>
      <li>Customized treatment plans</li>
      <li>Integrated, co-ordinated care</li>
      <li>Evidence-based care applying leading best practices</li>
      <li>Access to specialty clinics: Physiatry and Chronic Pain</li>
    </ul>
  </div>

  <div class="panel contact">
    <p class="contact__call">Please call us <strong>555-384-2096</strong><br>for more information on injury<br>rehabilitation</p>
    <p class="contact__address">Vela Mend Group<br>1862 Wexmoor Rd., Unit 9<br>Scarborough, ON K4T 8B2</p>
    <div class="contact__map" role="img" aria-label="Line-art street map showing the clinic location"></div>
    <p class="contact__referral"><strong>To make a referral for your clients,<br>contact:</strong>velamendgroup@corvamail.ca<br>fax: Thank you.</p>
    <p class="contact__web">www.velamendgroup.ca</p>
  </div>

  <div class="panel cover">
    <div class="cover__photo" role="img" aria-label="Photo of a woman running outdoors in front of mountains"></div>
    <svg class="cover__swoosh" width="190" height="438" viewBox="0 0 190 438" aria-hidden="true">
      <path d="M0 390 C 80 380, 150 350, 190 318 L190 438 L0 438 Z" fill="var(--white)"/>
    </svg>
    <h1 class="cover__title">
      <span class="t-light">Integrated</span><br>
      <span class="t-green">Injury</span><br>
      <span class="t-blue">Rehab</span>
    </h1>
    <p class="cover__tagline">Evidence-based,<br>one-on-one care to<br>make your recovery<br>fast and comfortable</p>
    <div class="seal" role="img" aria-label="Award seal"></div>
    <div class="brand"><span class="brand__dot"></span>Vela Mend</div>
    <p class="cover__web">www.velamendgroup.ca</p>
  </div>
</section>

<section class="sheet sheet--inside">
  <div class="panel team">
    <div class="portrait portrait--lead" role="img" aria-label="Portrait of Dr. Harriet Olsavik in a white coat"></div>
    <div class="member m1">
      <h3 class="member__name">Harriet Olsavik, MD,</h3>
      <p class="member__cred">FRCPC, MSC, CIME<br>Physiatrist</p>
      <p class="member__bio">Dr. Olsavik specializes in injury rehab and sports medicine. She is highly trained having received her MD and Residency in Physiatry from Pellham Institute. Her passion is to help injured people get back to their life.</p>
    </div>
    <div class="team__rule"></div>
    <div class="portrait portrait--second" role="img" aria-label="Portrait of physiotherapist Wendy Carstairs"></div>
    <div class="member m2">
      <h3 class="member__name">Wendy Carstairs, PT</h3>
      <p class="member__cred">Physiotherapist</p>
      <p class="member__bio">Wendy has over 10 years of experience as a Physiotherapist (5 in Canada). She has advanced training in orthopedics and manual therapy. She loves and relates well with people from the youngest to the most senior.</p>
    </div>
  </div>

  <div class="panel services">
    <div class="services__photo" role="img" aria-label="Photo of a therapist fitting a knee brace on a patient"></div>
    <h2 class="services__title">Our services</h2>
    <p class="services__intro">We provide integrated assessment and care from interprofessional team of regulated healthcare professionals with proven experience in injury rehabilitation:</p>
    <ul class="services__list">
      <li>Physiatrists</li>
      <li>Sport medicine</li>
      <li>Physicians</li>
      <li>Physiotherapists</li>
      <li>Chiropractors</li>
      <li>Massage therapists</li>
      <li>Acupuncturists</li>
      <li>Psychologists</li>
    </ul>
    <div class="services__rule"></div>
    <p class="services__extras">We provide custom medical<br>bracing, orthotics, orthopedic<br>shoes, assistive devices, and<br>medical stockings, all in one place.</p>
  </div>

  <div class="panel promise">
    <p class="promise__block promise__block--first">Only registered physiotherapists<br>We strongly believe in consistency with your treatment plan. This means that you spend your time here one-on-one with your physiotherapist, not any students or assistants. You get consistent high quality care from a professional.</p>
    <div class="promise__rule" style="top:153px"></div>
    <p class="promise__block promise__block--second">One-on-one attention<br>We book maximum 3 people per hour to ensure everyone gets adequate one-on-one time with their physiotherapist. This compares favorably with other clinics, who may book upwards of 5-6 per hour. The atmosphere is professional -balanced with friendly, caring and relaxed. Our highly qualified staff operate this way to help make your recovery faster and more enjoyable.</p>
    <div class="promise__rule" style="top:334px"></div>
    <div class="seal" role="img" aria-label="Award seal"></div>
    <div class="brand"><span class="brand__dot"></span>Vela Mend</div>
  </div>
</section>

</body>
</html>
```